We need a business card design for a new company located in Missouri City, TX, entitled 'BrightPath Chiropractic & Holistic Center'. Our services include restoration of health and vitality, spinal exam, health assessment, dietary & fitness programs, lymphatic & therapeutic massage, detox & remineralize body wraps, far infrared sauna therapy

Industry/Entity Type

Business

Contact Information for Business Card

BrightPath Chiropractic & Holistic Center, Marlene Okafor LMT, 4215 Elm Ridge Rd., Suite 310, Missouri City, TX 77482, 281-555-0193

```html
<!DOCTYPE html>
<html lang="en">
<head>
<meta charset="utf-8">
<title>BrightPath Chiropractic &amp; Holistic Center – Business Card</title>
<link rel="stylesheet" href="https://fonts.googleapis.com/css2?family=Marcellus&family=Arimo:wght@400&display=swap">
<style>
  :root {
    --page-bg: #e9e7e3;
    --card-white: #f7f7f7;
    --teal: #1f9e87;
    --teal-dark: #17836f;
    --navy: #1c5783;
    --navy-light: #2a6d9c;
    --ink-grey: #5b5b5b;
    --band-black: #111111;
    --white: #ffffff;
  }
  * { box-sizing: border-box; margin: 0; padding: 0; }
  html, body { width: 1200px; height: 902px; overflow: hidden; }
  body {
    background: var(--page-bg);
    display: flex;
    align-items: center;
    justify-content: center;
    gap: 40px;
    font-family: "Arimo", Arial, sans-serif;
  }
  .card {
    position: relative;
    width: 540px;
    height: 309px;
    border-radius: 4px;
    overflow: hidden;
    box-shadow: 0 6px 18px rgba(0,0,0,0.18);
  }

  /* Back: services */
  .card-back {
    background: linear-gradient(160deg, var(--navy-light) 0%, var(--navy) 60%);
    color: var(--white);
    padding: 34px 38px;
  }
  .services-title {
    font-size: 27px;
    letter-spacing: 0.5px;
    margin-bottom: 12px;
  }
  .services-list { list-style: none; }
  .services-list li {
    position: relative;
    font-size: 17px;
    line-height: 30px;
    padding-left: 30px;
    color: #eef4f9;
  }
  .services-list li::before {
    content: "";
    position: absolute;
    left: 6px;
    top: 11px;
    width: 8px;
    height: 8px;
    border-radius: 50%;
    background: var(--white);
  }

  /* Front */
  .card-front { background: var(--card-white); }
  .front-shapes { position: absolute; inset: 0; }
  .brand {
    position: absolute;
    top: 38px;
    left: 0;
    width: 100%;
    text-align: center;
    font-family: "Marcellus", Georgia, serif;
    color: var(--ink-grey);
  }
  .brand-mark {
    display: block;
    width: 26px;
    height: 26px;
    margin: 0 auto 10px;
    border-radius: 50%;
    background: var(--teal);
  }
  .brand-name { font-size: 34px; line-height: 1.1; }
  .brand-name span { display: block; font-size: 34px; }
  .brand-name .brand-sub { font-size: 19px; }

  .holder {
    position: absolute;
    left: 34px;
    top: 228px;
    color: var(--white);
  }
  .holder-name {
    font-family: "Marcellus", Georgia, serif;
    font-size: 25px;
    line-height: 1.1;
  }
  .holder-role { font-size: 16px; margin-top: 2px; }

  .contacts {
    position: absolute;
    left: 300px;
    top: 222px;
    border-left: 1.5px solid var(--white);
    padding-left: 12px;
    list-style: none;
    color: var(--white);
  }
  .contacts li {
    display: flex;
    align-items: center;
    gap: 9px;
    font-size: 12.5px;
    line-height: 19px;
  }
  .contact-icon { width: 13px; height: 13px; flex: none; }

  .address {
    position: absolute;
    left: 34px;
    bottom: 12px;
    font-size: 11.5px;
    color: var(--white);
  }
</style>
</head>
<body>

  <section class="card card-back" aria-label="Business card back – services">
    <h2 class="services-title">Services :</h2>
    <ul class="services-list">
      <li>Restoration of health and vitality</li>
      <li>Spinal exam</li>
      <li>Health assessment</li>
      <li>Dietary &amp; fitness programs</li>
      <li>Lymphatic &amp; therapeutic massage</li>
      <li>Detox &amp; remineralize body wraps</li>
      <li>Far infrared sauna therapy</li>
    </ul>
  </section>

  <section class="card card-front" aria-label="Business card front">
    <svg class="front-shapes" width="540" height="309" viewBox="0 0 540 309" aria-hidden="true">
      <path d="M0,212 L30,222 L462,222 L540,104 L540,309 L0,309 Z" fill="var(--teal)"/>
      <path d="M40,214 L455,214 L518,118" fill="none" stroke="var(--band-black)" stroke-width="6" stroke-linejoin="miter"/>
    </svg>

    <div class="brand">
      <span class="brand-mark"></span>
      <p class="brand-name">
        <span>BrightPath</span>
        <span class="brand-sub">Chiropractic &amp; Holistic Center</span>
      </p>
    </div>

    <div class="holder">
      <p class="holder-name">Priya Lindqvist</p>
      <p class="holder-role">Director</p>
    </div>

    <ul class="contacts">
      <li>
        <svg class="contact-icon" viewBox="0 0 16 16" aria-hidden="true"><rect x="0.5" y="0.5" width="15" height="15" fill="none" stroke="#fff"/><path d="M4 3 L6 3 L7 6 L5.5 7 Q7 10 9 10.5 L10 9 L13 10 L13 12 Q8 13 4 7 Z" fill="#fff"/></svg>
        281-555-0193
      </li>
      <li>
        <svg class="contact-icon" viewBox="0 0 16 16" aria-hidden="true"><rect x="0.5" y="0.5" width="15" height="15" fill="none" stroke="#fff"/><circle cx="8" cy="8" r="4.5" fill="none" stroke="#fff"/><path d="M3.5 8 H12.5 M8 3.5 V12.5" stroke="#fff"/></svg>
        www.brightpathcare.com
      </li>
      <li>
        <svg class="contact-icon" viewBox="0 0 16 16" aria-hidden="true"><rect x="0.5" y="0.5" width="15" height="15" fill="none" stroke="#fff"/><rect x="3" y="4.5" width="10" height="7" fill="none" stroke="#fff"/><path d="M3 4.5 L8 8.5 L13 4.5" fill="none" stroke="#fff"/></svg>
        plindqvist@brightpathcare.com
      </li>
    </ul>

    <p class="address">Marlene Okafor LMT, 4215 Elm Ridge Rd., Suite 310, Missouri City, TX 77482</p>
  </section>

</body>
</html>
```